Amber Loop Subscription Box Design, with Greeting Card, Booklet and Web Banners.

We need a PRINT READY box design with theme: ITALY
(Inner and outer sides)
The box contains Food & Beverage products coming directly from Italy.

Size: 80cmx35cmx16cm (attached for template). Yes, it's a big box, it has the wow factor, see the ClipNest screenshot example - referring to the size only - it has the wow unboxing factor.

ONCE WE AGREE ON THE BOX DESIGN, we then need the below deliverables using the design adaptation from the Box:
- Greeting card
- 12-page booklet (See Mirel*va examples) - photos and copy will be provided.
- 3x Web/App Banners (See M*re*lva examples) - the elements will need to be able to be used across different banner dimensions/sizes (a square, rectangle, etc. so for product hero shot, cover image, banner ads, story image, image listing, blog image, etc.).

The booklet structure is as follows:
(Total 1,000 words)
- Cover page
- (2 page spread) Intro 200 words max + Main Image
- A map indicating product origins
- (Across 5 pages) 2 products per page, 50-75 words each product + image
- (2 page spread) Community Development Innitiatives - 200 words max, a few images
- Back cover

After Italy, we will be doing India, China, Japan, Thailand, Mexico and Greece. So please keep in mind when designing the Italy Box as we need to allow a nice colour palette for the Amber Loop range.

Our company logo and other details will be provided.
Cheers

Tech, F&B, Travel

• Style: Clean, minimalistic, sophisticated, a mix of contemporary & Traditional, and sustainable. Imagine receiving and unboxing an Quell product, we need the same wow effect. On the outside: we need to have the App Logo (attached with the colour code), along with 3x small USP icons (Australian Owned, HACCP certified, and Recyclable), and small text: "Country of Origin: ITALY". You can adjust the colour of the icons to suit. We also need to be deliberate and bold with our messaging for "EAT ORIGINAL. PRESERVE HERITAGE", so we need this text either on the outer or inner of the box. Due to size of the box, placing this slogan on the inside when customer is unboxing may be ideal. Also on the inside: The usual social sharing icons with hashtag info. Feel free to add an instruction icons on how to unbox - in order to deliver an unmatched immersive experience.
• Background illustration graphics on Italian heritage/landmark buildings, towers, etc is an option. ANOTHER EXAMPLE: Just to give an example of a cool box design, though we need to stick to the Box Style brief above, is from Fobbit - see attached.
• Busy design, too flashy, graphics that are not representative of an Italian range.

```html
<!DOCTYPE html>
<html lang="en">
<head>
<meta charset="utf-8">
<title>Amber Loop Italy Box – Inside Dieline</title>
<link rel="stylesheet" href="https://fonts.googleapis.com/css2?family=Figtree:wght@400;500;600;800;900&display=swap">
<style>
  :root {
    --paper: #ffffff;
    --board: #f0ede6;
    --green: #3d7a5c;
    --landmark-light: #dedad3;
    --dieline: #d6ecd3;
    --mark: #555555;
    --bleed: #6dbb4a;
    --trim: #27306b;
    --crease: #e0312f;
  }
  * { margin: 0; padding: 0; box-sizing: border-box; }
  html, body { width: 1200px; height: 983px; overflow: hidden; background: var(--paper); }
  .sheet { position: relative; width: 1200px; height: 983px; font-family: "Figtree", sans-serif; color: var(--green); }
  .dieline { position: absolute; inset: 0; }
  .side-label { position: absolute; left: 28px; top: 48px; font-size: 38px; font-weight: 500; letter-spacing: -0.5px; }
  .spec-table { position: absolute; left: 64px; top: 0; display: grid; grid-template-columns: 38px 38px 30px 40px; column-gap: 0; font-size: 2.6px; line-height: 3.6px; color: #333; font-weight: 600; }
  .spec-table i { display: inline-block; width: 12px; height: 1px; vertical-align: middle; margin-left: 3px; }
  .slogan { position: absolute; left: 315px; top: 178px; font-size: 43px; font-weight: 900; line-height: 49px; letter-spacing: -0.5px; text-transform: uppercase; }
  .landmarks { position: absolute; left: 528px; top: 219px; width: 369px; height: 212px;
    background: linear-gradient(180deg, var(--board) 0%, var(--landmark-light) 35%, #7fa18c 70%, var(--green) 100%); }
  .closing-line { position: absolute; left: 0; width: 1200px; top: 628px; text-align: center; font-size: 52px; font-weight: 500; line-height: 54px; letter-spacing: -0.3px; }
  .closing-line strong { font-weight: 900; }
  .web-address { position: absolute; left: 0; width: 1200px; top: 772px; text-align: center; font-size: 14px; font-weight: 600; }
  .side-note { position: absolute; left: 0; width: 1200px; top: 955px; text-align: center; font-size: 5px; font-weight: 600; color: #222; }
</style>
</head>
<body>
<div class="sheet">
  <svg class="dieline" width="1200" height="983" viewBox="0 0 1200 983" aria-hidden="true">
    <g fill="none" stroke="var(--dieline)" stroke-width="0.8">
      <path d="M176 166 L176 120 C176 58 226 34 290 34 L910 34 C974 34 1024 58 1024 120 L1024 166"/>
      <rect x="167" y="164" width="866" height="270"/>
      <rect x="180" y="432" width="840" height="118"/>
      <rect x="34" y="550" width="1132" height="275"/>
      <rect x="180" y="825" width="840" height="124"/>
    </g>
    <g fill="var(--board)">
      <path d="M180 162 L180 122 C180 62 230 38 290 38 L910 38 C970 38 1020 62 1020 122 L1020 162 Z"/>
      <polygon points="294,162 176,205 171,212 171,384 176,390 294,431 906,431 1024,390 1029,384 1029,212 1024,205 906,162"/>
      <rect x="183" y="431" width="834" height="120"/>
      <rect x="291" y="545" width="618" height="285"/>
      <rect x="40" y="555" width="1119" height="266"/>
      <rect x="38" y="594" width="4" height="36"/>
      <rect x="38" y="670" width="4" height="36"/>
      <rect x="38" y="746" width="4" height="36"/>
      <rect x="1158" y="594" width="4" height="36"/>
      <rect x="1158" y="670" width="4" height="36"/>
      <rect x="1158" y="746" width="4" height="36"/>
      <rect x="184" y="823" width="831" height="122"/>
    </g>
    <g stroke="var(--mark)" stroke-width="0.6" fill="none">
      <path d="M31 30 L31 34 L35 34"/>
      <path d="M1169 30 L1169 34 L1165 34"/>
      <path d="M31 953 L31 949 L35 949"/>
      <path d="M1169 953 L1169 949 L1165 949"/>
    </g>
  </svg>

  <div class="spec-table">
    <span>Inside size</span><span>800 x 350 x 160</span><span>Remark</span><span>Rev 10</span>
    <span>Outside size</span><span>816 x 364 x 163</span><span>Box No.</span><span>1479 x 1198</span>
    <span>Make size</span><span>810 x 352 x 162</span><span>Design Area</span><span>None</span>
    <span>Material</span><span>E-flute paper</span><span>Film</span><span></span>
    <span>Thickness</span><span>1.6mm</span><span></span><span></span>
    <span>BLEED<i style="background:var(--bleed)"></i></span><span>TRIM<i style="background:var(--trim)"></i></span><span style="color:var(--crease)">CREASE</span><span></span>
  </div>

  <div class="side-label">Inside</div>

  <h1 class="slogan">Eat<br>Original.<br>Preserve<br>Heritage</h1>

  <div class="landmarks" role="img" aria-label="Illustrated Italian skyline: the Colosseum, Leaning Tower of Pisa, domed basilica, obelisk, sun, clouds and birds"></div>

  <p class="closing-line">Want more? You<br>know <strong>where</strong> to find us</p>
  <p class="web-address">www.amberloop.io</p>

  <p class="side-note">Outer</p>
</div>
</body>
</html>
```